Business Card Design for Flood Rescue 360 - Property Restoration Professionals

I need a business card designed for Flood Rescue 360. We are a full-service property restoration solution. Providing water, fire, smoke & storm restoration as well as mold remediation and full remodel or reconstruction to homes and businesses across Dallas-Fort Worth, TX.
Target Market(s)
home and business owners with insurance covered property damage from water, fire or storm related damage
Industry/Entity Type
property restoration
Contact Information for Business Card
Marcus Pelley General Manager Cell: 214-555-0193 Office: 469-555-0148 email: Marcus@FloodRescue360.example services: Water, Fire, Mold, Reconstruction Tagline: Urgency for Your Water Emergency!
Look and feel
Each slider illustrates characteristics of the customer's brand and the style your logo design should communicate.

```html
<!DOCTYPE html>
<html lang="en">
<head>
<meta charset="utf-8">
<title>Flood Rescue 360 – Business Card</title>
<link rel="stylesheet" href="https://fonts.googleapis.com/css2?family=Montserrat:wght@400;500;600;700&display=swap">
<style>
  :root {
    --brand-blue: #00b2e3;
    --ink: #1a1a1a;
    --paper: #ffffff;
    --backdrop: #ecebea;
  }
  * { box-sizing: border-box; margin: 0; padding: 0; }
  html, body {
    width: 1200px; height: 768px; overflow: hidden;
    background: var(--backdrop);
    font-family: "Montserrat", sans-serif;
  }
  .stage { position: relative; width: 1200px; height: 768px; }
  .card {
    position: absolute; top: 230px;
    width: 540px; height: 309px;
    box-shadow: 0 6px 18px rgba(0,0,0,.12);
    overflow: hidden;
  }
  .card--back { left: 40px; background: var(--paper); }
  .card--front { left: 620px; background: var(--brand-blue); }

  /* company name */
  .company { font-weight: 700; line-height: 1; white-space: nowrap; }

  /* front */
  .card--front .company {
    position: absolute; left: 0; right: 0; top: 118px;
    text-align: center; color: var(--paper); font-size: 40px;
  }
  .tagline {
    position: absolute; left: 0; right: 0; top: 186px;
    text-align: center; color: var(--paper);
    font-weight: 700; font-size: 12px; letter-spacing: .3px;
  }

  /* back */
  .card--back .company {
    position: absolute; right: 42px; top: 62px;
    color: var(--brand-blue); font-size: 28px;
  }
  .person { position: absolute; left: 40px; top: 118px; }
  .person__name { color: var(--brand-blue); font-weight: 700; font-size: 21px; line-height: 1.2; }
  .person__title { color: var(--ink); font-size: 11px; margin-top: 2px; }
  .rule {
    position: absolute; left: 40px; right: 42px; top: 168px;
    height: 1.5px; background: var(--brand-blue);
  }
  .contacts { position: absolute; left: 40px; top: 180px; list-style: none; }
  .contacts li {
    display: flex; align-items: center; gap: 8px;
    font-size: 11.5px; color: var(--ink); line-height: 19px;
  }
  .contacts svg { width: 11px; height: 11px; fill: var(--brand-blue); flex: none; }
  .services {
    position: absolute; right: 42px; bottom: 28px;
    font-weight: 600; font-size: 12px; color: var(--ink);
  }
  .services .sep { color: var(--brand-blue); margin: 0 3px; }
  .band {
    position: absolute; left: 0; right: 0; bottom: 0; height: 9px;
    background: var(--brand-blue);
  }
</style>
</head>
<body>
<main class="stage">
  <section class="card card--back" aria-label="Business card, contact side">
    <p class="company">Flood Rescue 360</p>
    <div class="person">
      <h1 class="person__name">Marcus Pelley</h1>
      <p class="person__title">General Manager</p>
    </div>
    <div class="rule"></div>
    <ul class="contacts">
      <li>
        <svg viewBox="0 0 24 24" aria-hidden="true"><path d="M6.6 10.8a15.1 15.1 0 0 0 6.6 6.6l2.2-2.2c.3-.3.7-.4 1-.2 1.1.4 2.3.6 3.6.6.6 0 1 .4 1 1V20c0 .6-.4 1-1 1A17 17 0 0 1 3 4c0-.6.4-1 1-1h3.5c.6 0 1 .4 1 1 0 1.3.2 2.5.6 3.6.1.3 0 .7-.2 1z"/></svg>
        214-555-0193
      </li>
      <li>
        <svg viewBox="0 0 24 24" aria-hidden="true"><path d="M4 9c0-2 3.6-4 8-4s8 2 8 4v1.5h-4V9H8v1.5H4zM6 12h12l2 7H4zm6 1.5a2.5 2.5 0 1 0 0 5 2.5 2.5 0 0 0 0-5z"/></svg>
        469-555-0148
      </li>
      <li>
        <svg viewBox="0 0 24 24" aria-hidden="true"><path d="M2 5h20v14H2zm2 2v.5l8 5 8-5V7z"/></svg>
        Marcus@FloodRescue360.example
      </li>
    </ul>
    <p class="services"><span class="sep">•</span>Water<span class="sep">•</span>Fire<span class="sep">•</span>Mold<span class="sep">•</span>Reconstruction</p>
    <div class="band"></div>
  </section>

  <section class="card card--front" aria-label="Business card, brand side">
    <p class="company">Flood Rescue 360</p>
    <p class="tagline">Urgency for Your Water Emergency!</p>
  </section>
</main>
</body>
</html>
```